Informational Site for Advanced Chemistry R&D

The company develops oxidation chemistry for air, water, fuel pollution controls. The site has been prototyped at www.velquaresearch.example. Take a look. Now, the task is to design it for eye-catching beauty with use of color, on-page scroll-driven color transition and parallax effects. Should capture the themes: high technology, wow it's beautiful, modern, uncluttered, clean urban environment.

Target Market(s)

China Environmentally Conscious Government and Industry,

Industry/Entity Type

It Company

Number of Pages Required

3 page

Font styles to use
Sans Serif

Requirements
Must have
• Parallax effects, desktop compatible, Rich, Modern, Simple, Graphic
Nice to have
• Mobile Phone Compatible
Should not have
• Flash, or anything that is slow to load or requires high bandwidth

```html
<!DOCTYPE html>
<html lang="en">
<head>
<meta charset="utf-8">
<title>Velqua — Advanced Oxidation Science</title>
<link href="https://fonts.googleapis.com/css2?family=Open+Sans:wght@300;400;600;700&display=swap" rel="stylesheet">
<style>
:root{
  --purple:#8e44c4;
  --purple-soft:#b57ad6;
  --pink:#cc74c6;
  --orange:#f4b168;
  --green:#7cc85a;
  --band:#f3f3f3;
  --lilac:#f6eef8;
  --ink:#444;
  --ink-soft:#555;
  --footer:#312c52;
  --footer-text:#a9a6c2;
  --white:#fff;
}
*{margin:0;padding:0;box-sizing:border-box}
html,body{width:1010px;height:1200px;overflow:hidden;background:var(--white)}
body{font-family:'Open Sans',sans-serif;position:relative;color:var(--ink)}
.abs{position:absolute}

/* hero */
.hero{left:0;top:0;width:1010px;height:325px;
  background:linear-gradient(115deg,var(--purple) 0%,#a652c8 25%,var(--pink) 48%,#e99a9a 62%,var(--orange) 78%,var(--orange) 100%);}
.brand{left:30px;top:46px;display:flex;align-items:center;gap:10px;color:var(--white);font-weight:700;font-size:30px;letter-spacing:.5px}
.brand-dot{width:26px;height:26px;border-radius:50%;background:var(--white)}
.nav{left:312px;top:27px;display:flex;gap:18px;font-size:9px;color:rgba(255,255,255,.85)}
.btn-ghost{border:1.5px solid var(--white);border-radius:12px;color:var(--white);font-size:8.5px;font-weight:700;height:19px;display:flex;align-items:center;justify-content:center}
.btn-free{left:657px;top:21px;width:107px}
.btn-sign{left:773px;top:22px;width:53px}
.hero-title{left:215px;top:48px;width:340px;text-align:center;color:var(--white);font-weight:300;font-size:26px;line-height:29.5px}
.hero-cta{left:184px;top:215px;width:146px;height:42px;border:1.5px solid var(--white);border-radius:22px;color:var(--white);font-weight:300;font-size:16px;display:flex;align-items:center;justify-content:center}
.hero-visual{left:633px;top:110px;width:193px;height:134px;border-radius:8px;background:linear-gradient(135deg,rgba(255,255,255,.55),rgba(255,255,255,.3))}
.dots{left:478px;top:299px;display:flex;gap:6px}
.dots span{width:9px;height:9px;border-radius:50%;border:1px solid var(--white)}
.dots span.on{background:var(--white)}

/* features */
.features{left:0;top:325px;width:1010px;height:177px;background:var(--band)}
.feature{top:355px;width:220px;text-align:center}
.feature svg{display:block;margin:0 auto;height:42px}
.feature h3{font-size:10.5px;font-weight:600;color:#333;margin-top:20px}
.feature p{font-size:10px;color:var(--ink-soft);margin-top:10px}
.feature a{display:block;font-size:10px;color:var(--purple);text-decoration:none;margin-top:11px}

/* signup */
.orb{border-radius:50%}
.orb-small{left:63px;top:667px;width:144px;height:144px;background:linear-gradient(180deg,#a952b8 0%,#d98a92 50%,var(--orange) 100%)}
.orb-big{left:-88px;top:572px;width:240px;height:240px;background:var(--purple)}
.orb-right{left:847px;top:610px;width:360px;height:356px;background:linear-gradient(180deg,var(--orange) 0%,var(--orange) 55%,#d98a92 78%,var(--purple) 100%)}
.target{left:463px;top:618px}
.signup-title{left:0;top:740px;width:1010px;text-align:center;font-size:30px;font-weight:300;color:var(--ink)}
.email{left:301px;top:822px;width:211px;height:45px;border:1px solid #ddd;border-radius:23px;font-size:11px;color:#999;padding-left:19px;display:flex;align-items:center}
.signup-btn{left:529px;top:822px;width:177px;height:45px;border-radius:23px;background:var(--purple);color:var(--white);font-size:13px;display:flex;align-items:center;justify-content:center}

/* customers */
.customers{left:0;top:1000px;width:1010px;height:147px;background:var(--lilac)}
.customers-title{left:0;top:1036px;width:1010px;text-align:center;font-size:14px;color:var(--purple)}
.client-row{left:205px;top:1085px;width:600px;display:flex;justify-content:space-between}
.client{font-size:17px;font-weight:700;color:var(--purple-soft)}

/* footer */
.footer{left:0;top:1147px;width:1010px;height:53px;background:var(--footer)}
.footer-links{left:292px;top:1169px;display:flex;gap:18px;font-size:9px;color:var(--footer-text)}
</style>
</head>
<body>

<section class="abs hero"></section>
<div class="abs brand"><span class="brand-dot"></span>Velqua</div>
<nav class="abs nav"><span>Product</span><span>Pricing</span><span>Support</span><span>Blog</span></nav>
<div class="abs btn-ghost btn-free">Get started for free</div>
<div class="abs btn-ghost btn-sign">Sign In</div>
<h1 class="abs hero-title">Advanced Oxidation Science for Environmental Pollution Management</h1>
<div class="abs hero-cta">Get started</div>
<div class="abs hero-visual" role="img" aria-label="Illustration of a design file converting into a web page layout"></div>
<div class="abs dots"><span class="on"></span><span></span><span></span><span></span></div>

<section class="abs features"></section>
<div class="abs feature" style="left:161px">
  <svg viewBox="0 0 44 42" aria-hidden="true"><rect x="1" y="6" width="32" height="22" rx="2" fill="var(--green)" transform="rotate(-12 17 17)"/><ellipse cx="32" cy="28" rx="9" ry="4" fill="var(--green)"/><ellipse cx="32" cy="33" rx="9" ry="4" fill="var(--green)"/><ellipse cx="32" cy="38" rx="9" ry="3.5" fill="var(--green)"/></svg>
  <h3>Feature-packed payments</h3>
  <p>Card storage, subscriptions, and more.</p>
  <a href="#">See all features</a>
</div>
<div class="abs feature" style="left:396px">
  <svg viewBox="0 0 42 42" aria-hidden="true"><path d="M24 2 L40 2 L40 18 L16 40 L2 26 Z" fill="var(--green)"/><circle cx="33" cy="9" r="3" fill="var(--band)"/></svg>
  <h3>Simple pricing</h3>
  <p>Leave complex fee structures behind.</p>
  <a href="#">Learn more</a>
</div>
<div class="abs feature" style="left:633px">
  <svg viewBox="0 0 44 42" aria-hidden="true"><path d="M4 34 A18 18 0 0 1 40 34" fill="none" stroke="var(--green)" stroke-width="6" stroke-dasharray="8 3"/><path d="M22 34 L28 12" stroke="var(--green)" stroke-width="4" stroke-linecap="round"/><circle cx="22" cy="34" r="4" fill="var(--green)"/></svg>
  <h3>Natively web &amp; mobile</h3>
  <p>JavaScript &amp; native libraries available.</p>
  <a href="#">View documentation</a>
</div>

<div class="abs orb orb-small"></div>
<div class="abs orb orb-big"></div>
<div class="abs orb orb-right"></div>
<svg class="abs target" width="84" height="84" viewBox="0 0 84 84" aria-hidden="true">
  <circle cx="42" cy="42" r="42" fill="#f1e6f7"/>
  <circle cx="42" cy="42" r="35" fill="#e7d3f1"/>
  <circle cx="42" cy="42" r="28" fill="var(--white)"/>
  <circle cx="42" cy="42" r="19" fill="none" stroke="var(--orange)" stroke-width="5"/>
  <circle cx="42" cy="42" r="4" fill="var(--purple)"/>
</svg>
<h2 class="abs signup-title">Make your life easier</h2>
<div class="abs email">sample@mail.com</div>
<div class="abs signup-btn">Get Started for FREE</div>

<section class="abs customers"></section>
<div class="abs customers-title">Our happy customers</div>
<div class="abs client-row">
  <span class="client">Pinora</span><span class="client">Chirply</span><span class="client">Shopwell</span><span class="client">Ryda</span><span class="client">Pinora</span><span class="client">Launchfund</span>
</div>

<footer class="abs footer"></footer>
<div class="abs footer-links"><span>Status Blog</span><span>About Jobs</span><span>Open Source</span><span>Contact</span><span>Privacy &amp; Terms</span></div>

</body>
</html>
```